Consulting company business cards

We have a base design, but would be willing to update. We have a new logo/"tag" that needs to be added. Current business card design is attached for reference into our "style."

Industry/Entity Type

Business

Contact Information for Business Card

Should contain name and title, office number, mobile number if appropriate, e-mail, website, physical address, and company logo.

Font styles to use
Other font styles liked:
• See current card design on KorvandBCard

Colors
0455a3
85acd3
aaaaaa

Requirements
Must have
• Our colors are navy blue, gray, and a lighter blue
Nice to have
• Design that I can easily drop in new names/titles as we hire employees.

```html
<!DOCTYPE html>
<html lang="en">
<head>
<meta charset="utf-8">
<title>Tallow Business Cards – KorvandBCard</title>
<link rel="stylesheet" href="https://fonts.googleapis.com/css2?family=Bebas+Neue&family=Open+Sans:wght@400;600&display=swap">
<style>
  :root {
    --navy: #002b49;
    --navy-back: #03304f;
    --light-blue: #7aabcb;
    --grey-text: #4a4a4a;
    --grey-line: #c9c9c9;
    --card-white: #ffffff;
    --stage: #2b2b2b;
  }
  * { margin: 0; padding: 0; box-sizing: border-box; }
  html, body { width: 1200px; height: 987px; overflow: hidden; }
  body {
    position: relative;
    background: var(--stage);
    font-family: "Open Sans", Arial, sans-serif;
  }
  .card {
    position: absolute;
    left: 293px;
    width: 615px;
    height: 352px;
    border-radius: 19px;
    overflow: hidden;
  }
  .card--front { top: 125px; background: var(--card-white); }
  .card--back { top: 510px; background: var(--navy-back); }

  .brand-name {
    position: absolute;
    left: 0;
    width: 318px;
    top: 146px;
    text-align: center;
    font-family: "Open Sans", Arial, sans-serif;
    font-weight: 600;
    font-size: 40px;
    line-height: 1;
    color: var(--navy);
  }

  .divider {
    position: absolute;
    left: 318px;
    top: 74px;
    width: 1px;
    height: 211px;
    background: var(--grey-line);
  }

  .contact {
    position: absolute;
    left: 344px;
    top: 72px;
  }
  .contact__name {
    font-family: "Bebas Neue", Impact, sans-serif;
    font-size: 31px;
    font-weight: 400;
    line-height: 1;
    letter-spacing: 0.5px;
    color: var(--navy);
  }
  .contact__title {
    font-family: "Bebas Neue", Impact, sans-serif;
    font-size: 21px;
    line-height: 1;
    letter-spacing: 0.5px;
    color: var(--light-blue);
    margin-top: 3px;
  }
  .contact__address {
    margin-top: 10px;
    font-size: 16px;
    line-height: 22px;
    color: var(--grey-text);
    font-style: normal;
  }
  .contact__list { list-style: none; margin-top: 4px; }
  .contact__item {
    display: flex;
    align-items: center;
    gap: 10px;
    font-size: 16px;
    line-height: 24px;
    color: var(--grey-text);
  }
  .contact__icon { width: 15px; height: 15px; fill: var(--navy); flex: none; }

  .back-name {
    position: absolute;
    left: 0; right: 0;
    top: 135px;
    text-align: center;
    font-family: "Open Sans", Arial, sans-serif;
    font-weight: 600;
    font-size: 56px;
    line-height: 1;
    color: var(--light-blue);
  }
  .back-url {
    position: absolute;
    left: 0; right: 0;
    top: 293px;
    text-align: center;
    font-size: 17px;
    letter-spacing: 3.5px;
    color: var(--card-white);
  }
</style>
</head>
<body>

  <section class="card card--front">
    <p class="brand-name">Tallow</p>

    <div class="divider"></div>

    <div class="contact">
      <h1 class="contact__name">DANAKORVAND</h1>
      <p class="contact__title">OFFICE MANAGER</p>
      <address class="contact__address">
        1187 N Elm Ridge Rd<br>
        Fairbrook Ohio 43210
      </address>
      <ul class="contact__list">
        <li class="contact__item">
          <svg class="contact__icon" viewBox="0 0 16 16"><path d="M3.6 1.2 6 3.6 4.6 5.6c.9 2.2 2.6 3.9 4.8 4.8l2-1.4 2.4 2.4-1.4 2.8C6.8 14.2 1.8 9.2 .8 3z"/></svg>
          555.014.2280
        </li>
        <li class="contact__item">
          <svg class="contact__icon" viewBox="0 0 16 16"><rect x="4" y="1" width="8" height="4"/><rect x="1" y="6" width="14" height="6" rx="1"/><rect x="4" y="10" width="8" height="5" fill="#fff"/><rect x="5" y="11" width="6" height="3"/></svg>
          555.014.2291
        </li>
        <li class="contact__item">
          <svg class="contact__icon" viewBox="0 0 16 16"><path d="M1 3h14v10H1z"/><path d="M1.5 3.5 8 9l6.5-5.5" fill="none" stroke="#fff" stroke-width="1.4"/></svg>
          dkorvand@tallowtech.com
        </li>
        <li class="contact__item">
          <svg class="contact__icon" viewBox="0 0 16 16"><circle cx="8" cy="8" r="7"/><path d="M1 8h14M8 1c-3 3-3 11 0 14M8 1c3 3 3 11 0 14" fill="none" stroke="#fff" stroke-width="1.1"/></svg>
          www.tallowtech.com
        </li>
      </ul>
    </div>
  </section>

  <section class="card card--back">
    <p class="back-name">Tallow</p>
    <p class="back-url">www.tallowtech.com</p>
  </section>

</body>
</html>
```